Create a Wordpress Design (Dorrel)

We need a wordpress design for an established auction and real estate company based in Tennessee. The winning design will incorporate a professional color scheme with company logo in a clean layout. The design needs to consider that this will be developed on a responsive theme. Colors are those that will highlight the logo.
Updates

This client, an older gentleman, wants the site to mimic http://www.quillfordbidhouse.example/. If you can adjust you designs with this site in mind - perhaps 3 columns, less color etc. We are trying to get him a concept that he likes and he keeps mentioning this site. Do not copy this site, but keep it in mind while re-doing the concept. Thanks, - auction services -

Industry/Entity Type

Real Estate

Font styles to use
Sans Serif

Colors

Designer to choose colors to be used in the design.

Requirements
Must have
• - Navigation: 1) Home - with auctions as content as seen at http://brenwickgavel.example/ 2) Properties for Sale 3) Auctions 4) Sell Your Property 5) Community Info 6) About Us 7) Contact Us

Color will be those that highlight logo in a professional creative way. Site tagline: "Our Signs are Everywhere". Site will have a slideshow - please use stock real estate image for the initial photo.

Widgets: 1) social media (FB twitter, linked In, Youtube, RSS) 2) News & Events blog, 3) testimonials 4) featured Property widget.

Footer will have contact info (below) smaller company logo, and the association logos attached, and contact info:
Phone: (615) 555-0178
Contacts: Marion Teague-Hollis
Email: marketing@kenwoodorrel.example
Address: 22-C Elmfield Court W, Murfreesboro, TN 37199

Nice to have
• use and styling of a dropdown menu: Under AUCTIONS, 1) Upcoming 2) Past

```html
<!DOCTYPE html>
<html lang="en">
<head>
<meta charset="utf-8">
<title>Dorrel Commercial Realtors, Auctioneers LLC</title>
<link href="https://fonts.googleapis.com/css2?family=Open+Sans:wght@400;600;700;800&display=swap" rel="stylesheet">
<style>
:root{
  --red:#c4161c;
  --red-dark:#8e0f13;
  --blue:#1f5fa8;
  --ink:#333333;
  --muted:#777777;
  --line:#dddddd;
  --panel:#f2f2f2;
  --dark:#2a2a2a;
  --darker:#1c1c1c;
  --white:#ffffff;
}
*{box-sizing:border-box;margin:0;padding:0}
html,body{width:1200px;height:2568px;overflow:hidden}
body{font-family:"Open Sans",Arial,sans-serif;color:var(--ink);background:var(--white);position:relative}
.wrap{width:960px;margin:0 auto;position:relative}

/* header */
.site-header{height:80px}
.brand{position:absolute;left:0;top:16px;display:flex;align-items:center;gap:10px}
.brand-dot{width:14px;height:14px;border-radius:50%;background:var(--red)}
.brand-name{font-size:34px;font-weight:800;color:var(--red);letter-spacing:2px;text-transform:uppercase}
.header-tools{position:absolute;right:0;top:24px;display:flex;gap:8px;align-items:center}
.social{width:26px;height:26px;background:var(--blue);border-radius:3px}
.login{margin-left:14px;background:var(--blue);color:var(--white);font-size:12px;font-weight:700;padding:7px 22px;border-radius:3px}

/* nav */
.main-nav{height:40px;position:relative;z-index:3}
.main-nav ul{list-style:none;display:flex;background:var(--red);height:40px}
.main-nav li{font-size:12px;font-weight:700;color:var(--white);text-transform:uppercase;padding:0 22px;line-height:40px;position:relative;border-right:1px solid rgba(255,255,255,.2)}
.main-nav li.active{background:var(--blue)}
.main-nav li.open{background:var(--red-dark)}
.dropdown{position:absolute;left:0;top:40px;width:140px;background:var(--red-dark)}
.dropdown span{display:block;line-height:26px;padding:0 14px;font-size:11px;font-weight:600;text-transform:none;border-top:1px solid rgba(255,255,255,.15)}

/* hero */
.hero{position:absolute;top:120px;left:0;width:1200px;height:580px;background:linear-gradient(180deg,#b9cbe0 0%,#8aa3c0 45%,#4f6075 75%,#3a4a36 100%)}
.hero-quote{position:absolute;left:190px;top:420px;background:rgba(20,20,20,.6);color:var(--white);padding:16px 22px;font-size:15px;font-weight:700;line-height:24px;text-transform:uppercase}
.hero-arrow{position:absolute;top:270px;width:34px;height:34px;border-radius:50%;background:rgba(255,255,255,.7)}
.hero-arrow svg{display:block;margin:9px}
.hero-arrow.prev{left:20px}.hero-arrow.next{right:20px}

/* welcome */
.welcome{position:absolute;top:700px;left:0;width:1200px;height:130px;text-align:center;padding-top:34px}
.welcome h1{font-size:17px;font-weight:800;text-transform:uppercase;color:var(--ink)}
.welcome p{width:880px;margin:12px auto 0;font-size:11px;line-height:18px;color:var(--muted)}

/* section ribbon headings */
.ribbon{position:relative;height:34px;text-align:center}
.ribbon::before{content:"";position:absolute;left:0;right:0;top:17px;height:1px;background:var(--line)}
.ribbon span{position:relative;display:inline-block;background:var(--red);color:var(--white);font-size:14px;font-weight:700;text-transform:uppercase;line-height:34px;padding:0 40px}
.ribbon.left{text-align:left}
.ribbon.left span{padding:0 24px}

/* featured */
.featured{position:absolute;top:830px;left:0;width:1200px}
.featured .cards{display:flex;gap:30px;margin-top:22px}
.prop-card{width:300px;background:var(--panel);border:1px solid var(--line)}
.prop-photo{height:170px;position:relative}
.prop-tag{position:absolute;left:0;bottom:0;background:var(--white);font-size:10px;font-weight:700;padding:4px 12px;text-transform:uppercase}
.prop-body{padding:10px 12px;height:64px}
.prop-body h3{font-size:12px;font-weight:700}
.prop-body p{font-size:10px;color:var(--muted);margin-top:4px}

/* features band */
.features{position:absolute;top:1160px;left:0;width:1200px;height:230px;background:linear-gradient(180deg,#1e2226 0%,#2c3138 55%,#3d3324 100%)}
.features .wrap{display:flex;justify-content:space-between;padding-top:50px}
.feature{width:210px;text-align:center;color:var(--white)}
.feature svg{display:block;margin:0 auto 12px}
.feature h4{font-size:12px;font-weight:700;text-transform:uppercase}
.feature p{font-size:10px;line-height:15px;color:#c9c9c9;margin-top:8px}

/* auctions */
.auctions{position:absolute;top:1410px;left:0;width:1200px}
.auctions .cards{display:flex;gap:40px;margin-top:24px;justify-content:center}
.auction-card{width:440px;height:190px;border:1px solid var(--line);background:var(--white);padding:14px;display:flex;gap:14px}
.auction-photo{width:170px;height:120px}
.auction-info h3{font-size:13px;font-weight:700}
.auction-info dl{font-size:10px;line-height:16px;margin-top:8px;display:grid;grid-template-columns:56px 1fr}
.auction-info dt{font-weight:700}
.auction-actions{position:absolute;margin-top:0}
.btn{display:inline-block;font-size:10px;font-weight:700;color:var(--white);padding:5px 14px;text-transform:uppercase}
.btn.red{background:var(--red)}.btn.blue{background:var(--blue)}
.card-col{position:relative}
.card-col .buttons{position:absolute;left:14px;bottom:14px;display:flex;gap:6px}

/* news + testimonials */
.duo{position:absolute;top:1690px;left:0;width:1200px}
.duo .wrap{display:flex;gap:40px}
.duo .col{width:460px}
.news-item{display:flex;gap:14px;margin-top:22px;position:relative}
.news-photo{width:150px;height:110px;position:relative;flex:none}
.news-date{position:absolute;right:-8px;bottom:10px;background:var(--red);color:var(--white);font-size:10px;font-weight:700;padding:4px 8px}
.news-item h3{font-size:12px;font-weight:700;line-height:17px}
.news-item p{font-size:10px;line-height:15px;color:var(--muted);margin-top:6px}
.testimonial{margin-top:22px;border:1px solid var(--line);padding:20px 22px;height:250px;position:relative}
.testimonial .mark{font-size:40px;font-weight:800;color:var(--line);line-height:30px}
.testimonial p{font-size:11px;line-height:18px;color:var(--muted);margin-top:4px}
.author{display:flex;align-items:center;gap:12px;margin-top:18px}
.avatar{width:46px;height:46px;border-radius:50%;background:#b89a86}
.author strong{font-size:11px;color:var(--red)}
.author span{font-size:10px;color:var(--muted)}
.t-nav{position:absolute;right:16px;bottom:16px;display:flex;gap:5px}
.t-nav i{width:20px;height:20px;border-radius:50%;background:var(--dark)}
.t-nav i.on{background:var(--red)}

/* associations */
.association{position:absolute;top:2045px;left:0;width:1200px}
.badges{display:flex;justify-content:space-between;margin-top:28px;padding:0 20px}
.badge{width:80px;height:56px;background:#d8d8d8;border-radius:4px}
.badge.round{border-radius:50%;width:56px}

/* footer */
.site-footer{position:absolute;top:2232px;left:0;width:1200px;height:336px;background:var(--dark);color:#bdbdbd}
.footer-main{display:flex;gap:40px;padding-top:40px}
.footer-brand{font-size:26px;font-weight:800;color:var(--white);letter-spacing:2px;text-transform:uppercase;width:180px}
.footer-main p{font-size:10px;line-height:17px;width:740px}
.contact-row{display:flex;gap:60px;margin-top:46px;font-size:11px;padding-top:20px;border-top:1px solid #3e3e3e}
.contact-row span{display:flex;align-items:center;gap:8px}
.footer-bottom{position:absolute;bottom:0;left:0;width:1200px;height:58px;background:var(--darker);font-size:10px}
.footer-bottom .wrap{display:flex;justify-content:space-between;line-height:58px}
</style>
</head>
<body>

<header class="site-header wrap">
  <div class="brand"><span class="brand-dot"></span><span class="brand-name">Dorrel</span></div>
  <div class="header-tools">
    <span class="social"></span><span class="social"></span><span class="social"></span><span class="social"></span>
    <span class="login">LOGIN</span>
  </div>
</header>

<nav class="main-nav wrap">
  <ul>
    <li class="active">Home</li>
    <li>Properties for Sale</li>
    <li class="open">Auctions
      <div class="dropdown"><span>Upcoming</span><span>Past</span></div>
    </li>
    <li>Sell Your Property</li>
    <li>Community Info</li>
    <li>About Us</li>
    <li>Contact Us</li>
  </ul>
</nav>

<section class="hero" role="img" aria-label="Stock photo of a downtown skyline with glass office towers">
  <div class="hero-quote">"We're proud of what we do, so put yourself at ease.<br>Take our experience, expertise and dedication home with you!"</div>
  <span class="hero-arrow prev"><svg width="16" height="16" viewBox="0 0 16 16"><path d="M10 2 4 8l6 6" fill="none" stroke="#333" stroke-width="2"/></svg></span>
  <span class="hero-arrow next"><svg width="16" height="16" viewBox="0 0 16 16"><path d="M6 2l6 6-6 6" fill="none" stroke="#333" stroke-width="2"/></svg></span>
</section>

<section class="welcome">
  <h1>Welcome to Dorrel Commercial Realtors, Auctioneers LLC</h1>
  <p>Our signs are everywhere. For decades our team has helped families and businesses across Middle Tennessee buy, sell and auction property with care. We handle homes, farms, land and commercial sites, and we guide every client from the first visit to the final bid with honest advice.</p>
</section>

<section class="featured">
  <div class="wrap">
    <div class="ribbon"><span>Featured Property</span></div>
    <div class="cards">
      <article class="prop-card">
        <div class="prop-photo" role="img" aria-label="Photo of a modern condo building at dusk" style="background:linear-gradient(180deg,#5d7fa6,#2f3e52)"><span class="prop-tag">Condo</span></div>
        <div class="prop-body"><h3>Majestic Residence in Alabama</h3><p>14 Lakeview Drive, Murfreesboro TN</p></div>
      </article>
      <article class="prop-card">
        <div class="prop-photo" role="img" aria-label="Photo of a two-storey country house with a lawn" style="background:linear-gradient(180deg,#a9c4dd,#7d8a63)"><span class="prop-tag">Lower Rise</span></div>
        <div class="prop-body"><h3>Splendid Country House</h3><p>305 Maple Hill Road, Murfreesboro TN</p></div>
      </article>
      <article class="prop-card">
        <div class="prop-photo" role="img" aria-label="Photo of a large white villa under blue sky" style="background:linear-gradient(180deg,#8fb4d8,#cfd3cc)"><span class="prop-tag">Villa</span></div>
        <div class="prop-body"><h3>Unique 1905-2000 Private Beach</h3><p>78 Harbor Lane, Murfreesboro TN</p></div>
      </article>
    </div>
  </div>
</section>

<section class="features" role="img" aria-label="Night city skyline behind the service icons">
  <div class="wrap">
    <div class="feature">
      <svg width="44" height="44" viewBox="0 0 44 44"><circle cx="18" cy="18" r="11" fill="none" stroke="#fff" stroke-width="3"/><path d="M26 26l12 12" stroke="#fff" stroke-width="4"/></svg>
      <h4>Search a Property</h4><p>Browse homes, land and commercial listings by type, price and size.</p>
    </div>
    <div class="feature">
      <svg width="44" height="44" viewBox="0 0 44 44"><path d="M22 40S9 25 9 17a13 13 0 0 1 26 0c0 8-13 23-13 23z" fill="#fff"/><circle cx="22" cy="17" r="5" fill="#2c3138"/></svg>
      <h4>Select by Location</h4><p>Find properties near the town, school or road that suits you best.</p>
    </div>
    <div class="feature">
      <svg width="44" height="44" viewBox="0 0 44 44"><path d="M6 8h32v22H18l-8 7v-7H6z" fill="#fff"/></svg>
      <h4>Live Support</h4><p>Talk with our agents during the week for quick, friendly answers.</p>
    </div>
    <div class="feature">
      <svg width="44" height="44" viewBox="0 0 44 44"><path d="M6 22 22 8l16 14v16H6z" fill="#fff"/><rect x="18" y="26" width="8" height="12" fill="#2c3138"/></svg>
      <h4>Get the Property</h4><p>Place your bid or make an offer and move in with confidence.</p>
    </div>
  </div>
</section>

<section class="auctions">
  <div class="wrap">
    <div class="ribbon"><span>Upcoming Auctions</span></div>
    <div class="cards">
      <article class="auction-card card-col">
        <div class="auction-photo" role="img" aria-label="Photo of a brick family home for auction" style="background:linear-gradient(180deg,#9db6cf,#8a6f55)"></div>
        <div class="auction-info">
          <h3>Lorem ipsum dolor sit</h3>
          <dl><dt>Begins:</dt><dd>June 30, 2013 at 7:00 PM CDT</dd><dt>Location:</dt><dd>711 Oak Ave<br>Murfreesboro, TN 37199<br>Phone 615-555-0178</dd></dl>
        </div>
        <div class="buttons"><span class="btn red">Details</span><span class="btn blue">Gallery</span></div>
      </article>
      <article class="auction-card card-col">
        <div class="auction-photo" role="img" aria-label="Photo of a suburban house with garden for auction" style="background:linear-gradient(180deg,#a7c0d8,#6d7f58)"></div>
        <div class="auction-info">
          <h3>Ut wisi enim ad minim</h3>
          <dl><dt>Begins:</dt><dd>June 30, 2013 at 7:00 PM CDT</dd><dt>Location:</dt><dd>711 Oak Ave<br>Murfreesboro, TN 37199<br>Phone 615-555-0178</dd></dl>
        </div>
        <div class="buttons"><span class="btn red">Details</span><span class="btn blue">Gallery</span></div>
      </article>
    </div>
  </div>
</section>

<section class="duo">
  <div class="wrap">
    <div class="col">
      <div class="ribbon left"><span>News &amp; Events</span></div>
      <article class="news-item">
        <div class="news-photo" role="img" aria-label="Photo of a modern apartment building" style="background:linear-gradient(180deg,#8fb0d2,#5b6f84)"><span class="news-date">AUG 15</span></div>
        <div><h3>Lorem ipsum dolor sit amet, consectetur adipiscing elit.</h3><p>New listings arrive this month across Rutherford County. Join us at the preview day to walk the homes before bidding opens.</p></div>
      </article>
      <article class="news-item">
        <div class="news-photo" role="img" aria-label="Photo of a small house beside a sold sign" style="background:linear-gradient(180deg,#c9d7e6,#b24a3e)"><span class="news-date">AUG 15</span></div>
        <div><h3>Sodales eget ipsum dolor sit amet magna aliqua.</h3><p>Our team shares tips for sellers getting ready for auction day, from staging to pricing and paperwork.</p></div>
      </article>
    </div>
    <div class="col">
      <div class="ribbon left"><span>Testimonials</span></div>
      <div class="testimonial">
        <div class="mark">"</div>
        <p>The whole team made selling our family farm simple. They explained every step, answered our calls at any hour and brought in more bidders than we ever expected. We got a fair price and the closing went smoothly. I would gladly recommend them to friends and neighbors.</p>
        <div class="author"><span class="avatar" role="img" aria-label="Client portrait placeholder"></span><div><strong>Renata</strong>, <span>Murfreesboro</span></div></div>
        <div class="t-nav"><i></i><i class="on"></i></div>
      </div>
    </div>
  </div>
</section>

<section class="association">
  <div class="wrap">
    <div class="ribbon"><span>Our Association</span></div>
    <div class="badges">
      <span class="badge round"></span><span class="badge"></span><span class="badge"></span><span class="badge round"></span>
      <span class="badge"></span><span class="badge round"></span><span class="badge"></span><span class="badge"></span>
    </div>
  </div>
</section>

<footer class="site-footer">
  <div class="wrap">
    <div class="footer-main">
      <div class="footer-brand">Dorrel</div>
      <p>Dorrel Commercial Realtors, Auctioneers LLC serves buyers and sellers throughout Middle Tennessee. Our licensed auctioneers and agents bring years of local knowledge to every sale, whether you are listing a home, a farm or a commercial building. Contact Marion Teague-Hollis to learn how we can help with your next move.</p>
    </div>
    <div class="contact-row">
      <span><svg width="12" height="14" viewBox="0 0 12 14"><path d="M6 14S0 8 0 5a6 6 0 0 1 12 0c0 3-6 9-6 9z" fill="#c4161c"/></svg>22-C Elmfield Court W, Murfreesboro, TN 37199</span>
      <span><svg width="12" height="12" viewBox="0 0 12 12"><path d="M2 0l3 3-2 2c1 2 2 3 4 4l2-2 3 3-2 2C5 12 0 7 0 2z" fill="#c4161c"/></svg>(615) 555-0178</span>
      <span><svg width="14" height="10" viewBox="0 0 14 10"><rect width="14" height="10" fill="#c4161c"/><path d="M0 0l7 6 7-6" fill="none" stroke="#2a2a2a"/></svg>marketing@kenwoodorrel.example</span>
    </div>
  </div>
  <div class="footer-bottom">
    <div class="wrap"><span>Home &nbsp;|&nbsp; Blog &nbsp;|&nbsp; About Us &nbsp;|&nbsp; Contact Us &nbsp;|&nbsp; Privacy Policy</span><span>Copyright © Dorrel Auctions. All Rights Reserved.</span></div>
  </div>
</footer>

</body>
</html>
```